K & R Acre Works. Business card design

We need a business card designed for a new business. We have a bulldozer and tractor service. We clear land and make wildlife food plots. We provide disking, bush hogging, and site prep services.
I have attached an image of a business card that I like and would like my business cards to look similar.

Target Market(s)

anyone needing bulldozer and/or tractor services

Industry/Entity Type

Business

Contact Information for Business Card

K & R Acre Works, Operated by 7-T-Ranch
Wade Colton
601-472-3358
wcr4817@fieldmail-example.com

Font styles to use
Sans Serif

Colors

Designer to choose colors to be used in the design.

Requirements
Must have
• image of tractor and bulldozer
• Land Clearing
• Wildlife food plots
• Bush Hogging
• Disking
• Site prep
Nice to have
• i have included a image of a business card that i like. I would like mine to be similar.

```html
<!DOCTYPE html>
<html lang="en">
<head>
<meta charset="utf-8">
<title>K &amp; R Acre Works – Business Card</title>
<link href="https://fonts.googleapis.com/css2?family=Roboto+Condensed:wght@400;700&family=Roboto:wght@400;500&display=swap" rel="stylesheet">
<style>
  :root {
    --page-bg: #2b2b2b;
    --card-bg: #f4f4f2;
    --olive: #9a9232;
    --brown: #6e3a12;
    --ink: #3c3c3c;
    --ink-dark: #2a2a2a;
    --sky: #8fb6dc;
    --machine-yellow: #d9b52a;
    --soil: #a88d68;
    --grass: #7f9a58;
    --tractor-red: #d8471f;
  }
  * { margin: 0; padding: 0; box-sizing: border-box; }
  html, body { width: 1200px; height: 771px; overflow: hidden; }
  body {
    background: var(--page-bg);
    position: relative;
    font-family: "Roboto", Arial, sans-serif;
  }
  .card {
    position: absolute;
    left: 300px; top: 214px;
    width: 600px; height: 343px;
    border-radius: 18px;
    background: var(--card-bg);
    overflow: hidden;
    box-shadow: 0 4px 10px rgba(0,0,0,.45);
  }
  .photo-dozer {
    position: absolute; left: 0; top: 0;
    width: 320px; height: 343px;
    background: linear-gradient(180deg, var(--sky) 0%, #b9cfe3 25%, var(--machine-yellow) 42%, #8a7a3a 60%, var(--soil) 78%, #c7b393 100%);
    -webkit-mask-image: linear-gradient(90deg, #000 60%, transparent 100%);
            mask-image: linear-gradient(90deg, #000 60%, transparent 100%);
  }
  .photo-tractor {
    position: absolute; left: 440px; top: 236px;
    width: 160px; height: 107px;
    background:
      radial-gradient(ellipse 45% 40% at 50% 55%, var(--tractor-red) 0%, rgba(216,71,31,.6) 55%, transparent 100%),
      linear-gradient(180deg, transparent 0%, #a9b88a 40%, var(--grass) 100%);
    -webkit-mask-image: linear-gradient(90deg, transparent 0%, #000 30%);
            mask-image: linear-gradient(90deg, transparent 0%, #000 30%);
  }
  .details { position: absolute; left: 300px; top: 0; width: 290px; }
  .brand-name {
    position: absolute; top: 51px; left: 1px;
    font-family: "Roboto Condensed", "Arial Narrow", sans-serif;
    font-weight: 700; font-size: 25px; letter-spacing: 1.2px;
    color: var(--olive); white-space: nowrap;
  }
  .tagline {
    position: absolute; top: 77px; left: 1px;
    font-family: "Roboto Condensed", "Arial Narrow", sans-serif;
    font-weight: 700; font-size: 11.5px; letter-spacing: .2px;
    color: var(--ink-dark); white-space: nowrap;
  }
  .person-name {
    position: absolute; top: 103px; left: 1px;
    font-family: "Roboto Condensed", "Arial Narrow", sans-serif;
    font-weight: 700; font-size: 21px; color: var(--olive);
  }
  .person-role {
    position: absolute; top: 127px; left: 1px;
    font-family: "Roboto Condensed", "Arial Narrow", sans-serif;
    font-weight: 700; font-size: 15px; color: var(--brown); white-space: nowrap;
  }
  .contact-list { position: absolute; top: 155px; left: 1px; list-style: none; }
  .contact-list li {
    display: flex; align-items: center; gap: 6px;
    height: 18px; font-size: 14px; color: var(--ink); white-space: nowrap;
  }
  .contact-list svg { width: 13px; height: 13px; fill: var(--olive); flex: none; }
  .services-title {
    position: absolute; top: 220px; left: 1px;
    font-family: "Roboto Condensed", "Arial Narrow", sans-serif;
    font-weight: 700; font-size: 18px; color: var(--olive);
  }
  .services-list { position: absolute; top: 241px; left: 1px; list-style: none; }
  .services-list li {
    height: 18px; font-size: 14.5px; color: var(--ink);
    display: flex; align-items: center; white-space: nowrap;
  }
  .bullet {
    display: inline-block; width: 5px; height: 5px; border-radius: 50%;
    background: var(--olive); margin-right: 7px;
  }
  .bullet.inline { margin: 0 4px; }
</style>
</head>
<body>
  <div class="card">
    <div class="photo-dozer" role="img" aria-label="Photo of a yellow bulldozer pushing a pile of dirt on a cleared site"></div>
    <div class="photo-tractor" role="img" aria-label="Photo of an orange compact tractor with a front loader in a grassy field"></div>

    <div class="details">
      <div class="brand-name">K &amp; R ACRE WORKS</div>
      <div class="tagline">FOR ALL OF YOUR LAND IMPROVEMENT NEEDS</div>

      <div class="person-name">WADE COLTON</div>
      <div class="person-role">OWNER · OPERATED BY 7-T-RANCH</div>

      <ul class="contact-list">
        <li>
          <svg viewBox="0 0 24 24" aria-hidden="true"><path d="M6.6 10.8a15.1 15.1 0 0 0 6.6 6.6l2.2-2.2c.3-.3.7-.4 1-.2 1.1.4 2.3.6 3.6.6.6 0 1 .4 1 1V20c0 .6-.4 1-1 1A17 17 0 0 1 3 4c0-.6.4-1 1-1h3.5c.6 0 1 .4 1 1 0 1.3.2 2.5.6 3.6.1.3 0 .7-.2 1z"/></svg>
          601-472-3358
        </li>
        <li>
          <svg viewBox="0 0 24 24" aria-hidden="true"><path d="M2 5h20v14H2z"/><path d="M2 6.5l10 7 10-7V5L12 12 2 5z" fill="#f4f4f2"/></svg>
          wcr4817@fieldmail-example.com
        </li>
        <li>
          <svg viewBox="0 0 24 24" aria-hidden="true"><circle cx="12" cy="12" r="10"/><path d="M7 8c2 0 3 1 3 3s-2 2-2 4 1 3 1 4M15 4c-1 2 0 3 2 3s3 2 2 4" stroke="#f4f4f2" stroke-width="1.6" fill="none"/></svg>
          kracreworks-example.com
        </li>
      </ul>

      <div class="services-title">WE PROVIDE</div>
      <ul class="services-list">
        <li><span class="bullet"></span>Land Clearing</li>
        <li><span class="bullet"></span>Wildlife food plots</li>
        <li><span class="bullet"></span>Bush Hogging</li>
        <li><span class="bullet"></span>Disking<span class="bullet inline"></span>Site prep</li>
      </ul>
    </div>
  </div>
</body>
</html>
```